Website for Vornelix Capital, my new firm that raises money from investors to buy, build, own an...

Vornelix Capital needs a website! We are a new company with very experienced people, who invest in, own and build hotel properties, as well as apartments and other commercial real estate. We seek investors for our projects, and we provide safe, secure returns on their investment in our projects. Our new logo is designed to exhibit strength, class and security, and would like our website to continue on this theme. Our name, Vornelix, is a word-play on a Greek word “aristeia”, which means “excellence” and “a warriors finest moment of glory in war”. If you are in business, you realize that much of it is like war, with strategy and moves and opponents and competitors, and ever-changing economic conditions and threats that make business very much like war. We like to think that we are good at business (war), and so have named our company “Vornelix”, using the founders last name and the word “aristeia” combined. Another definition of "aristeia" is "performing at the peak of one's potential after a long struggle"...again, much like business in real life! The website design should exhibit financial security, smart moves, and positive growth towards a bright future.

Target Market(s)

The target market is smart and wealthy investors, with others such as brokers, cities and government agencies, lenders, sellers, partners, etc also looking at it.

Industry/Entity Type

Investment

Number of Pages Required

5+ page

Font styles to use
Sans Serif

Colors
fec214

Requirements
Must have
• Our website should have a landing page, a "about" or bio page, a projects page and a contact us page. Our new logo uses the colors black and gold, so this should be factored in to our site. The site should be simple, yet impactful and impressive. I have actually two logos, which can be mixed and interchanged in a complimentary way, each with their own unique look.
Nice to have
• I have uploaded a couple screenshots of a website i like, and the simplicity I mention.
Should not have
• The site should not be flashy or complicated or complex or "busy"

```html
<!DOCTYPE html>
<html lang="en">
<head>
<meta charset="utf-8">
<title>Vornelix Capital</title>
<link href="https://fonts.googleapis.com/css2?family=Lato:ital,wght@0,300;0,400;0,700;0,900;1,400;1,700&display=swap" rel="stylesheet">
<style>
:root{
  --gold:#c5992f;
  --gold-bright:#d2a537;
  --ink:#111111;
  --charcoal:#2f2f2f;
  --text:#555555;
  --white:#ffffff;
  --line:#dddddd;
}
*{box-sizing:border-box;margin:0;padding:0}
html,body{width:1200px;height:3203px;overflow:hidden}
body{position:relative;background:var(--white);font-family:"Lato",sans-serif;color:var(--text)}
.abs{position:absolute}

/* header */
.site-header{left:0;top:0;width:1200px;height:113px;background:var(--white);z-index:5}
.brand{left:92px;top:36px;display:flex;align-items:center;gap:8px;font-weight:900;font-size:19px;color:var(--ink);letter-spacing:1px}
.brand-dot{width:12px;height:12px;background:var(--gold)}
.nav-home{left:262px;top:0;width:105px;height:133px;background:var(--gold);clip-path:polygon(0 0,100% 0,100% 100%,50% 88%,0 100%);color:var(--white);font-size:17px;text-align:center;padding-top:47px;z-index:6}
.nav-link{top:47px;font-size:17px;color:#444}
.search{left:726px;top:36px;width:237px;height:43px;border:1px solid var(--line);border-radius:22px;font-style:italic;font-size:13px;color:#777;padding:13px 0 0 16px}
.search svg{position:absolute;right:16px;top:12px}
.social-circle{top:36px;width:43px;height:43px;border-radius:50%;background:#333}

/* hero */
.hero{left:0;top:113px;width:1200px;height:575px;background:linear-gradient(120deg,#6b5a48 0%,#9a8876 35%,#bcae9a 55%,#8a7457 80%,#d6a65a 100%)}
.hero-shade{left:0;top:113px;width:1200px;height:575px;background:rgba(40,30,20,.35)}
.hero-title{left:0;top:228px;width:1200px;text-align:center;font-weight:300;font-size:54px;letter-spacing:6px;color:var(--white)}
.hero-sub{left:250px;top:316px;width:700px;text-align:center;font-style:italic;font-weight:700;font-size:15px;line-height:28px;color:var(--white)}

.service{top:446px;width:281px;height:291px;clip-path:polygon(0 0,100% 0,100% 85%,0 100%);color:var(--white);text-align:center;padding:28px 14px 0;z-index:3}
.service h3{font-weight:400;font-size:21px;margin:14px 0 12px}
.service p{font-size:14px;line-height:24px}
.service.dark{left:177px;background:var(--charcoal)}
.service.gold{left:458px;background:var(--gold)}
.service.black{left:739px;background:var(--ink)}

/* about */
.about-bg{left:0;top:688px;width:1200px;height:530px;background:linear-gradient(110deg,#e9e6e2 0%,#f3f1ee 45%,#dcd6cf 100%);clip-path:polygon(0 0,100% 0,100% 80%,0 100%)}
.about-title{left:0;top:798px;width:1200px;text-align:center;font-weight:900;font-size:37px;color:var(--gold)}
.about-text{left:268px;top:862px;width:664px;text-align:center;font-size:14px;line-height:25px;color:#666}
.btn{width:172px;height:56px;background:var(--ink);clip-path:polygon(12% 0,100% 0,88% 100%,0 100%);color:var(--white);font-size:17px;text-align:center;line-height:56px}

/* projects */
.section-title{left:0;top:1238px;width:1200px;text-align:center;font-weight:900;font-size:37px;color:var(--gold)}
.project{width:332px;height:332px;border:2px solid #e4e4e4;border-radius:22px;background:var(--white);box-shadow:0 2px 6px rgba(0,0,0,.08);padding:10px}
.project-photo{width:100%;height:100%;border-radius:18px}

/* testimonial */
.testimonial{left:0;top:2128px;width:1200px;height:560px;background:linear-gradient(100deg,#3d3a37 0%,#5a524a 40%,#3b3835 70%,#6a5c4c 100%);clip-path:polygon(0 22%,100% 0,100% 100%,0 100%)}
.quote-mark{left:578px;top:2230px}
.quote-text{left:300px;top:2296px;width:600px;text-align:center;font-size:16px;line-height:30px;color:var(--white)}
.avatar{left:552px;top:2386px;width:104px;height:104px;border-radius:50%;border:4px solid var(--white);background:linear-gradient(160deg,#cfc3b6,#8c7a6a)}
.quote-name{left:0;top:2522px;width:1200px;text-align:center;font-size:19px;color:var(--gold)}

/* footer */
.footer-band{left:0;top:2573px;width:1200px;height:512px;background:var(--gold);clip-path:polygon(0 19%,100% 0,100% 83%,0 100%)}
.footer-brand{left:100px;top:2745px;display:flex;align-items:center;gap:8px;font-weight:900;font-size:22px;color:var(--white);letter-spacing:1px}
.footer-brand .brand-dot{background:var(--white)}
.footer-about{left:79px;top:2844px;width:230px;font-size:14px;line-height:25px;color:var(--white)}
.footer-link{color:var(--white);text-decoration:underline;font-size:14px}
.footer-head{top:2710px;font-weight:700;font-size:20px;color:var(--white);letter-spacing:.5px}
.links{left:348px;top:2760px;list-style:none;color:var(--white);font-size:15px}
.links li{height:32px;display:flex;align-items:center;gap:12px}
.links li::before{content:"";width:7px;height:7px;background:var(--white)}
.contact-row{left:617px;color:var(--white);font-size:15px;line-height:32px;display:flex;gap:16px}
.post-meta{left:886px;top:2770px;font-style:italic;font-size:14px;color:var(--white)}
.post-meta b{font-style:italic}
.post-title{left:886px;top:2798px;width:260px;font-size:20px;line-height:28px;color:var(--white)}
.post-text{left:886px;top:2862px;width:240px;font-size:14px;line-height:25px;color:var(--white)}
.pager{top:2948px;width:18px;height:18px;border:1.5px solid var(--white)}
.social-tab{top:3038px;width:82px;height:58px;background:var(--ink);clip-path:polygon(25% 0,100% 0,75% 100%,0 100%)}
.copyright{left:0;top:3140px;width:1200px;text-align:center;font-size:14px;color:#555}
.copyright b{color:var(--ink)}
</style>
</head>
<body>

<header class="abs site-header">
  <div class="abs brand"><span class="brand-dot"></span>VORNELIX</div>
  <span class="abs nav-link" style="left:400px">ABOUT</span>
  <span class="abs nav-link" style="left:493px">PROJECTS</span>
  <span class="abs nav-link" style="left:610px">CONTACT</span>
  <div class="abs search">Search here.......
    <svg width="18" height="18" viewBox="0 0 18 18"><circle cx="7.5" cy="7.5" r="5.5" fill="none" stroke="#c5992f" stroke-width="2"/><line x1="11.5" y1="11.5" x2="16" y2="16" stroke="#c5992f" stroke-width="2"/></svg>
  </div>
  <div class="abs social-circle" style="left:988px" aria-label="Social link"></div>
  <div class="abs social-circle" style="left:1034px" aria-label="Social link"></div>
  <div class="abs social-circle" style="left:1080px" aria-label="Social link"></div>
</header>
<div class="abs nav-home">HOME</div>

<section>
  <div class="abs hero" role="img" aria-label="Business people shaking hands in an office"></div>
  <div class="abs hero-shade"></div>
  <h1 class="abs hero-title">VORNELIX</h1>
  <p class="abs hero-sub">Lorem Ipsum is simply dummy text of the printing and typesetting industry. Lorem Ipsum has been the industry's standard dummy text ever since the 1500s,</p>

  <div class="abs service dark">
    <svg width="60" height="62" viewBox="0 0 60 62" fill="none" stroke="#fff" stroke-width="2"><rect x="8" y="10" width="44" height="50"/><rect x="14" y="2" width="32" height="8"/><rect x="15" y="18" width="8" height="7"/><rect x="26" y="18" width="8" height="7"/><rect x="37" y="18" width="8" height="7"/><rect x="15" y="31" width="8" height="7"/><rect x="26" y="31" width="8" height="7"/><rect x="37" y="31" width="8" height="7"/><rect x="25" y="45" width="10" height="15"/></svg>
    <h3>Build Hotel Properties</h3>
    <p>Lorem Ipsum is simply dummy text of the printing and typesetting industry.</p>
  </div>
  <div class="abs service gold">
    <svg width="60" height="62" viewBox="0 0 60 62" fill="none" stroke="#fff" stroke-width="2"><rect x="8" y="2" width="28" height="58"/><rect x="36" y="22" width="18" height="38"/><rect x="14" y="10" width="6" height="6"/><rect x="24" y="10" width="6" height="6"/><rect x="14" y="22" width="6" height="6"/><rect x="24" y="22" width="6" height="6"/><rect x="14" y="34" width="6" height="6"/><rect x="24" y="34" width="6" height="6"/><rect x="41" y="30" width="8" height="6"/><rect x="41" y="42" width="8" height="6"/><rect x="18" y="48" width="8" height="12"/></svg>
    <h3>Build Apartments</h3>
    <p>Lorem Ipsum is simply dummy text of the printing and typesetting industry.</p>
  </div>
  <div class="abs service black">
    <svg width="60" height="62" viewBox="0 0 60 62" fill="none" stroke="#fff" stroke-width="2"><polyline points="4,32 30,8 56,32"/><polyline points="12,26 12,58 48,58 48,26"/><rect x="24" y="40" width="12" height="18"/><line x1="6" y1="12" x2="6" y2="58"/><polygon points="6,4 1,14 11,14"/></svg>
    <h3>Commercial Real Estate</h3>
    <p>Lorem Ipsum is simply dummy text of the printing and typesetting industry.</p>
  </div>
</section>

<section>
  <div class="abs about-bg" role="img" aria-label="Team meeting around a table, softly faded"></div>
  <h2 class="abs about-title">ABOUT VORNELIX</h2>
  <p class="abs about-text">Lorem Ipsum is simply dummy text of the printing and typesetting industry. Lorem Ipsum has been the industry's standard dummy text ever since the 1500s, when an unknown printer took a galley of type and scrambled it to make a type specimen book. It has survived not only five centuries, but also the leap into electronic typesetting, remaining essentially unchanged. It was popularised in the 1960s with the release of Letraset sheets containing Lorem Ipsum passages.</p>
  <div class="abs btn" style="left:515px;top:1023px">READ MORE</div>
</section>

<section>
  <h2 class="abs section-title">OUR LATEST PROJECTS</h2>
  <div class="abs project" style="left:79px;top:1326px"><div class="project-photo" role="img" aria-label="Colleagues reviewing charts at a desk" style="background:linear-gradient(135deg,#33485e,#c9d2d9 60%,#8896a3)"></div></div>
  <div class="abs project" style="left:434px;top:1326px"><div class="project-photo" role="img" aria-label="Smiling colleagues in a meeting" style="background:linear-gradient(135deg,#dfe6eb,#9aa8b3 55%,#4e5a65)"></div></div>
  <div class="abs project" style="left:790px;top:1326px"><div class="project-photo" role="img" aria-label="Team celebrating with a high five" style="background:linear-gradient(135deg,#f2e1c0,#a88a6a 50%,#3d3a3a)"></div></div>
  <div class="abs project" style="left:79px;top:1689px"><div class="project-photo" role="img" aria-label="Two colleagues discussing a tablet" style="background:linear-gradient(135deg,#2f4a63,#8aa3b5 50%,#c7b8a4)"></div></div>
  <div class="abs project" style="left:434px;top:1689px"><div class="project-photo" role="img" aria-label="Business team standing with documents" style="background:linear-gradient(135deg,#cfd8dc,#5a6166 55%,#2c3033)"></div></div>
  <div class="abs project" style="left:790px;top:1689px"><div class="project-photo" role="img" aria-label="Smiling businesswoman at a table" style="background:linear-gradient(135deg,#f5ead8,#c8ad88 50%,#5f6a74)"></div></div>
  <div class="abs btn" style="left:512px;top:2065px">VIEW ALL</div>
</section>

<section>
  <div class="abs testimonial" role="img" aria-label="Colleagues working on laptops in a dim office"></div>
  <svg class="abs quote-mark" width="52" height="40" viewBox="0 0 52 40"><path d="M0 40V22C0 8 6 2 18 0v7c-6 2-8 6-8 12h8v21z M28 40V22C28 8 34 2 46 0v7c-6 2-8 6-8 12h8v21z" fill="#c5992f"/></svg>
  <p class="abs quote-text">Lorem Ipsum is simply dummy text of the printing and typesetting industry. Lorem Ipsum has been the industry's standard dummy text ever since the 1500s.</p>
  <svg class="abs" style="left:300px;top:2418px" width="16" height="42" viewBox="0 0 16 42"><polyline points="14,1 2,21 14,41" fill="none" stroke="#fff" stroke-width="2"/></svg>
  <svg class="abs" style="left:854px;top:2418px" width="16" height="42" viewBox="0 0 16 42"><polyline points="2,1 14,21 2,41" fill="none" stroke="#fff" stroke-width="2"/></svg>
  <div class="abs avatar" role="img" aria-label="Client portrait"></div>
  <p class="abs quote-name">Daniel Rourke</p>
</section>

<footer>
  <div class="abs footer-band"></div>
  <div class="abs footer-brand"><span class="brand-dot"></span>VORNELIX</div>
  <p class="abs footer-about">Lorem Ipsum is simply dummy the text of the printing and Printing of<br><span class="footer-link">READ MORE</span></p>

  <h4 class="abs footer-head" style="left:348px">USEFUL LINKS</h4>
  <ul class="abs links"><li>Home</li><li>About</li><li>Projects</li><li>Contact</li></ul>

  <h4 class="abs footer-head" style="left:617px">GET IN TOUCH</h4>
  <div class="abs contact-row" style="top:2758px">
    <svg width="20" height="32" viewBox="0 0 20 32"><path d="M4 8c2-2 4-1 5 1l1 3c0 1-1 2-2 3 1 3 3 5 6 6 1-1 2-2 3-2l3 1c2 1 3 3 1 5-5 4-20-11-17-17z" fill="#fff"/></svg>
    <span>+1 555 010 2400</span></div>
  <div class="abs contact-row" style="top:2808px">
    <svg width="20" height="32" viewBox="0 0 20 32"><rect x="1" y="9" width="18" height="13" fill="#fff"/><polyline points="1,9 10,17 19,9" fill="none" stroke="#c5992f" stroke-width="1.5"/></svg>
    <span>info@vornelixcapital.com</span></div>
  <div class="abs contact-row" style="top:2848px">
    <svg width="20" height="32" viewBox="0 0 20 32"><path d="M10 4a7 7 0 0 0-7 7c0 6 7 13 7 13s7-7 7-13a7 7 0 0 0-7-7z" fill="#fff"/><circle cx="10" cy="11" r="2.5" fill="#c5992f"/><line x1="4" y1="28" x2="16" y2="28" stroke="#fff" stroke-width="2"/></svg>
    <span>123, Address, State Name<br>City, Street, Zipcode</span></div>

  <h4 class="abs footer-head" style="left:886px">RECENT POSTS</h4>
  <p class="abs post-meta"><b>26 September 2018</b> By Author</p>
  <p class="abs post-title">Excepteur sint occaecat cupidatat</p>
  <p class="abs post-text">Lorem Ipsum is simply dummy text of the printing and sed do eiusmod typesetting industry.<br><span class="footer-link" style="display:inline-block;margin-top:14px">READ MORE</span></p>
  <div class="abs pager" style="left:1021px"><svg width="15" height="15" viewBox="0 0 15 15"><polyline points="9,3 5,7.5 9,12" fill="none" stroke="#fff" stroke-width="1.5"/></svg></div>
  <div class="abs pager" style="left:1045px"><svg width="15" height="15" viewBox="0 0 15 15"><polyline points="6,3 10,7.5 6,12" fill="none" stroke="#fff" stroke-width="1.5"/></svg></div>

  <div class="abs social-tab" style="left:487px" aria-label="Social link"></div>
  <div class="abs social-tab" style="left:559px" aria-label="Social link"></div>
  <div class="abs social-tab" style="left:631px" aria-label="Social link"></div>

  <p class="abs copyright">Copyright © <b>VORNELIX CAPITAL</b> - 2018. All Right Reserved</p>
</footer>

</body>
</html>
```